FunBrixo Business Card

We need a business card design for our company. We sell construction-themed amusement rides for kids.

Contact Information for Business Card

Contact info on business card should include:
Carl Dunning
Co-Founder & COO
(833) 571-FUNBRIX
Carl@funbrixo-demo.com
www.funbrixo-demo.com

```html
<!DOCTYPE html>
<html lang="en">
<head>
<meta charset="utf-8">
<title>FunBrixo Business Card</title>
<link rel="stylesheet" href="https://fonts.googleapis.com/css2?family=Oswald:wght@300;400;500&display=swap">
<style>
  :root {
    --page-bg: #d9d6d2;
    --card-dark: #0e0e10;
    --card-dark-edge: #2b2b2e;
    --card-light: #e7e5e2;
    --card-light-edge: #c8c5c1;
    --orange: #e8651f;
    --blue: #1f7fd0;
    --pink: #e5287a;
    --purple: #7a2d8e;
    --gold: #d99a2b;
    --ink: #2a2a2c;
    --title: #c9572a;
  }
  * { box-sizing: border-box; margin: 0; padding: 0; }
  html, body { width: 1200px; height: 969px; overflow: hidden; }
  body { background: var(--page-bg); position: relative; font-family: "Oswald", sans-serif; }

  .card {
    position: absolute; left: 100px; top: 200px;
    width: 1000px; height: 570px;
    border-radius: 22px; overflow: hidden;
    background: linear-gradient(160deg, var(--card-light) 0%, var(--card-light-edge) 100%);
    box-shadow: 0 18px 40px rgba(0,0,0,.25);
  }
  .card-waves { position: absolute; inset: 0; width: 100%; height: 100%; }

  .brand {
    position: absolute; left: 84px; top: 120px;
    display: flex; align-items: center; gap: 18px;
  }
  .brand-dot { width: 40px; height: 40px; border-radius: 50%; background: var(--orange); }
  .brand-name { font-weight: 500; font-size: 76px; line-height: 1; color: var(--orange); letter-spacing: 1px; }

  .mascot {
    position: absolute; left: 100px; top: 418px; width: 100px; height: 122px;
    border-radius: 46px 46px 18px 18px;
    background: linear-gradient(180deg, #e7a13a 0%, #2a56a6 45%, #20418a 100%);
  }
  .machine-sketch {
    position: absolute; left: 600px; top: 243px; width: 400px; height: 317px;
    background: radial-gradient(ellipse at 60% 60%, rgba(120,118,115,.22), rgba(120,118,115,0) 70%);
  }

  .contact-block {
    position: absolute; right: 70px; top: 270px; text-align: right;
  }
  .person-name { font-weight: 500; font-size: 60px; line-height: 1; letter-spacing: 3px; }
  .person-name .c1 { color: var(--orange); }
  .person-name .c2 { color: var(--blue); }
  .person-name .c3 { color: var(--purple); }
  .person-name .c4 { color: var(--pink); }
  .person-name .c5 { color: var(--gold); }
  .person-role { font-weight: 400; font-size: 26px; letter-spacing: 2.5px; color: var(--title); margin-top: 8px; }

  .contact-list { list-style: none; margin-top: 36px; margin-right: -36px; }
  .contact-item {
    display: flex; justify-content: flex-end; align-items: center; gap: 12px;
    font-weight: 400; font-size: 20px; letter-spacing: 1.5px; color: var(--ink);
    height: 34px; text-transform: uppercase;
  }
  .contact-icon { width: 22px; height: 22px; flex: none; }
</style>
</head>
<body>
  <article class="card">
    <svg class="card-waves" viewBox="0 0 1000 570" preserveAspectRatio="none" aria-hidden="true">
      <defs>
        <linearGradient id="darkFill" x1="0" y1="0" x2="1" y2="1">
          <stop offset="0" stop-color="#2b2b2e"/>
          <stop offset=".4" stop-color="#0e0e10"/>
          <stop offset="1" stop-color="#1a1a1c"/>
        </linearGradient>
      </defs>
      <path d="M0 0 H1000 V150 C820 130 700 145 560 255 C430 360 300 515 0 515 Z" fill="url(#darkFill)"/>
      <path d="M0 545 C300 545 440 390 575 285 C700 185 820 165 1000 180" fill="none" stroke="var(--orange)" stroke-width="7"/>
      <path d="M0 532 C300 532 435 378 565 272 C695 170 820 150 1000 165" fill="none" stroke="var(--purple)" stroke-width="8"/>
      <path d="M0 522 C300 522 430 368 562 262 C695 160 820 142 1000 158" fill="none" stroke="var(--pink)" stroke-width="6"/>
      <path d="M0 515 C300 515 430 360 560 255 C700 145 820 130 1000 150" fill="none" stroke="var(--blue)" stroke-width="7"/>
      <path d="M60 505 C300 505 425 352 555 248 C700 138 820 122 1000 140" fill="none" stroke="var(--orange)" stroke-width="4"/>
    </svg>

    <div class="machine-sketch" role="img" aria-label="Faint line drawing of an excavator"></div>

    <div class="brand">
      <span class="brand-dot"></span>
      <span class="brand-name">FunBrixo</span>
    </div>

    <div class="mascot" role="img" aria-label="Cartoon mascot in a hard hat peeking over the wave"></div>

    <div class="contact-block">
      <h1 class="person-name"><span class="c1">C</span><span class="c2">A</span><span class="c3">R</span><span class="c4">L</span> <span class="c5">D</span><span class="c1">U</span><span class="c2">N</span><span class="c3">N</span><span class="c4">I</span><span class="c5">N</span><span class="c1">G</span></h1>
      <p class="person-role">CO-FOUNDER &amp; COO</p>
      <ul class="contact-list">
        <li class="contact-item">(833) 571-FUNBRIX
          <svg class="contact-icon" viewBox="0 0 24 24"><path fill="var(--orange)" d="M6.6 10.8a15.1 15.1 0 0 0 6.6 6.6l2.2-2.2c.3-.3.7-.4 1-.2 1.1.4 2.3.6 3.6.6.6 0 1 .4 1 1V20c0 .6-.4 1-1 1A17 17 0 0 1 3 4c0-.6.4-1 1-1h3.5c.6 0 1 .4 1 1 0 1.3.2 2.5.6 3.6.1.3 0 .7-.2 1z"/></svg>
        </li>
        <li class="contact-item">Carl@funbrixo-demo.com
          <svg class="contact-icon" viewBox="0 0 24 24"><rect x="2" y="5" width="20" height="14" rx="1.5" fill="var(--orange)"/><path d="M3 6l9 7 9-7" fill="none" stroke="#e7e5e2" stroke-width="1.6"/></svg>
        </li>
        <li class="contact-item">www.funbrixo-demo.com
          <svg class="contact-icon" viewBox="0 0 24 24"><circle cx="12" cy="12" r="10" fill="var(--orange)"/><path d="M2 12h20M12 2c3 3 3 17 0 20M12 2c-3 3-3 17 0 20" fill="none" stroke="#e7e5e2" stroke-width="1.4"/></svg>
        </li>
      </ul>
    </div>
  </article>
</body>
</html>
```